I need a SEO-friendly Wordpress website (making sure to style H1, H2, H3, etc correctly) for a Hawaii-based law firm called Meridian Crest Legal Group. Comparable websites include https://brvlaw.example/ and https://www.lomrit.example/ for design reference. The current copy on the TarnAdvocate.example website can be used.

```html
<!DOCTYPE html>
<html lang="en">
<head>
<meta charset="utf-8">
<title>Meridian Crest Legal Group – Divorce and Personal Injury Lawyers</title>
<link rel="stylesheet" href="https://fonts.googleapis.com/css2?family=Cinzel:wght@400;500&family=Libre+Baskerville:wght@400;700&family=Nunito+Sans:wght@300;400;600&display=swap">
<style>
:root{
  --brown:#7b2d04;
  --brown-title:#8a3608;
  --orange:#b45f0c;
  --orange-sub:#b0600f;
  --ink:#222;
  --text:#6b6b6b;
  --grey:#e2e3e5;
  --white:#fff;
}
*{margin:0;padding:0;box-sizing:border-box}
html,body{width:1200px;height:2396px;overflow:hidden;background:var(--white)}
body{position:relative;font-family:"Nunito Sans",Arial,sans-serif;color:var(--ink)}
.abs{position:absolute}
a{color:inherit;text-decoration:none}

/* Hero */
.hero{position:absolute;left:0;top:0;width:1200px;height:583px;
  background:linear-gradient(120deg,#d9c8a0 0%,#efe7cf 30%,#c9a9a6 55%,#9c6f82 80%,#b6899b 100%)}
.hero-title{position:absolute;left:600px;top:243px;transform:translateX(-50%);height:62px;padding:0 17px;background:var(--brown-title);
  color:var(--white);font-family:"Libre Baskerville",Georgia,serif;font-weight:700;font-size:32px;
  display:flex;align-items:center;justify-content:center;white-space:nowrap;letter-spacing:-.3px}
.hero-sub{position:absolute;left:397px;top:316px;width:406px;height:41px;background:var(--orange-sub);
  color:var(--white);font-size:20.5px;letter-spacing:.8px;display:flex;align-items:center;justify-content:center;white-space:nowrap}

/* Navigation */
.main-nav{position:absolute;left:0;top:583px;width:1200px;height:52px;background:var(--brown)}
.main-nav a{position:absolute;top:0;height:52px;line-height:52px;color:var(--white);font-size:13.5px;letter-spacing:.3px;white-space:nowrap}
.nav-home{left:77px;width:104px;text-align:center;background:var(--orange)}
.nav-cta{left:915px;width:208px;text-align:center;background:var(--orange)}

/* Section headings */
.section-title{position:absolute;left:0;width:1200px;text-align:center;font-family:"Cinzel",Georgia,serif;font-weight:400;color:#1a1a1a;font-size:34px;letter-spacing:1px}
.section-rule{position:absolute;left:574px;width:52px;height:2px;background:var(--orange)}
.intro{position:absolute;left:205px;top:777px;width:790px;text-align:center;font-size:13.5px;line-height:25px;color:var(--text)}

/* Practice cards */
.practice-card{position:absolute;top:891px;width:240px}
.practice-card .photo{width:240px;height:177px}
.practice-card h3{font-weight:400;font-size:20px;margin:24px 0 0 2px;color:#222}
.practice-card p{font-size:13.5px;line-height:25px;color:var(--text);margin:14px 0 0 3px}
.read-more{display:flex;align-items:center;gap:10px;margin:12px 0 0 2px;font-size:13.5px;color:#333;text-decoration:underline}

/* Call band */
.call-band{position:absolute;left:0;top:1302px;width:1200px;height:146px;background:var(--grey);border:1px solid #d3d3d5}
.call-band svg.band-shape{position:absolute;left:0;top:0}
.call-label{position:absolute;left:81px;top:1357px;color:var(--white);font-family:"Cinzel",Georgia,serif;font-size:25px;letter-spacing:1px;white-space:nowrap}
.call-number{position:absolute;left:328px;top:1357px;color:var(--white);font-family:"Libre Baskerville",Georgia,serif;font-size:23px;white-space:nowrap}
.call-info{position:absolute;left:680px;top:1328px;font-size:15px;line-height:27px;color:var(--text)}
.call-email{position:absolute;left:682px;top:1394px;display:flex;align-items:center;gap:16px;color:var(--brown);font-size:16.5px}

/* Blog */
.post-card{position:absolute;top:1619px;width:323px}
.post-card .photo{width:323px;height:229px}
.post-card h3{font-weight:400;font-size:17.5px;line-height:29px;margin:23px 0 0 2px;color:#222}
.post-card p{font-size:13.5px;line-height:25.5px;color:var(--text);margin:16px 0 0 2px}

/* Footer */
.site-footer{position:absolute;left:0;top:2104px;width:1200px;height:229px;background:var(--orange);color:var(--white)}
.footer-links a{position:absolute;top:42px;font-size:13.5px;white-space:nowrap}
.footer-rule{position:absolute;left:78px;top:95px;width:1047px;height:1px;background:rgba(120,45,5,.55)}
.contact-item{position:absolute;top:133px;display:flex;align-items:center;gap:20px;font-size:13.5px;line-height:25px}
.contact-icon{width:56px;height:56px;border-radius:50%;background:var(--brown);display:flex;align-items:center;justify-content:center;flex:none}
.copyright{position:absolute;left:0;top:2333px;width:1200px;height:63px;background:var(--brown);color:var(--white);font-size:13.5px;text-align:center;line-height:63px}
</style>
</head>
<body>

<header>
  <div class="hero" role="img" aria-label="Upward view of tall city office towers against a bright hazy sky"></div>
  <h1 class="hero-title">Meridian Crest Legal Group</h1>
  <p class="hero-sub">Divorce and Personal Injury Lawyers</p>
  <nav class="main-nav">
    <a class="nav-home" href="#">HOME</a>
    <a style="left:206px" href="#">PRACTICE AREAS</a>
    <a style="left:379px" href="#">ATTORNEYS</a>
    <a style="left:519px" href="#">BLOG</a>
    <a style="left:616px" href="#">CONTACT US</a>
    <a class="nav-cta" href="#">GET AN APPOINTMENT</a>
  </nav>
</header>

<main>
  <section class="practice-areas">
    <h2 class="section-title" style="top:680px">Practice Areas</h2>
    <div class="section-rule" style="top:742px"></div>
    <p class="intro">The Big Island based attorneys of Tarn Advocates are licensed in several states, and specialize in numerous areas including divorce, family &amp; custody, personal injury, wrongful death, real estate, contract, and intellectual property.</p>

    <article class="practice-card" style="left:77px">
      <div class="photo" role="img" aria-label="Family at home during a difficult conversation" style="background:linear-gradient(135deg,#d8d2c4,#efece4 60%,#c9c2b2)"></div>
      <h3>Family &amp; Divorce</h3>
      <p>Our lawyers handle all aspects of family law on the Big Island and...</p>
      <a class="read-more" href="#">READ MORE <svg width="26" height="10" viewBox="0 0 26 10"><path d="M0 5h24M19 1l5 4-5 4" fill="none" stroke="#333" stroke-width="1.4"/></svg></a>
    </article>
    <article class="practice-card" style="left:346px">
      <div class="photo" role="img" aria-label="Injured man with a cast resting on a sofa" style="background:linear-gradient(135deg,#e4e6e6,#9fb3c4 55%,#2f5f8a)"></div>
      <h3>Personal Injury</h3>
      <p>Dealing with personal injury and wrongful death claims is hard...</p>
      <a class="read-more" href="#">READ MORE <svg width="26" height="10" viewBox="0 0 26 10"><path d="M0 5h24M19 1l5 4-5 4" fill="none" stroke="#333" stroke-width="1.4"/></svg></a>
    </article>
    <article class="practice-card" style="left:614px">
      <div class="photo" role="img" aria-label="Business people shaking hands in a meeting room" style="background:linear-gradient(135deg,#b9c7d3,#5a6f86 50%,#1f2c3d)"></div>
      <h3>Corporate &amp; IP</h3>
      <p>The attorneys at MCLG have been helping Big Island business...</p>
      <a class="read-more" href="#">READ MORE <svg width="26" height="10" viewBox="0 0 26 10"><path d="M0 5h24M19 1l5 4-5 4" fill="none" stroke="#333" stroke-width="1.4"/></svg></a>
    </article>
    <article class="practice-card" style="left:883px">
      <div class="photo" role="img" aria-label="City skyline under a clear blue sky" style="background:linear-gradient(180deg,#4f86c8,#79a4d6 55%,#4b4a46)"></div>
      <h3>Real Estate</h3>
      <p>Our lawyers work with home owners, buyers and property developers to...</p>
      <a class="read-more" href="#">READ MORE <svg width="26" height="10" viewBox="0 0 26 10"><path d="M0 5h24M19 1l5 4-5 4" fill="none" stroke="#333" stroke-width="1.4"/></svg></a>
    </article>
  </section>

  <section class="call-band" aria-label="Call us">
    <svg class="band-shape" width="601" height="146" viewBox="0 0 601 146"><path d="M0 0H570L600 73L570 146H0Z" fill="#7b2d04"/></svg>
  </section>
  <p class="call-label">CALL US ON</p>
  <svg class="abs" style="left:252px;top:1346px" width="58" height="58" viewBox="0 0 58 58">
    <circle cx="29" cy="29" r="27.5" fill="none" stroke="#fff" stroke-width="1.5"/>
    <path d="M22 19c1.5-1 3-1 3.8.4l2 3.4c.6 1 .3 2-.6 2.7l-1.4 1c.9 2.6 2.8 4.6 5.4 5.6l1-1.4c.7-.9 1.800-1.2 2.7-.6l3.4 2c1.4.8 1.4 2.3.4 3.8-1.3 1.8-3.4 2.4-5.6 1.6-5.2-1.9-9.4-6.1-11.3-11.3-.8-2.2-.2-4.3 1.6-5.600z" fill="#fff"/>
  </svg>
  <p class="call-number">+1.808.555.0142</p>
  <p class="call-info">Over 70 years of combined practice, specializing in:<br>Personal Injury, Family &amp; Divorce, Child Custody</p>
  <a class="call-email" href="#"><svg width="26" height="19" viewBox="0 0 26 19"><rect width="26" height="19" rx="2" fill="#7b2d04"/><path d="M1 2l12 9 12-9" fill="none" stroke="#e2e3e5" stroke-width="2"/></svg>clients@tarnadvocate.example</a>

  <section class="blog">
    <h2 class="section-title" style="top:1506px">BLOG POST</h2>
    <div class="section-rule" style="top:1565px"></div>

    <article class="post-card" style="left:77px">
      <div class="photo" role="img" aria-label="Lawyer signing documents at a desk beside a laptop" style="background:linear-gradient(135deg,#2e2a25,#6c6358 50%,#1f1c19)"></div>
      <h3>Lorem ipsum dolor sit amet, consecte adipiscing elit, sed do eiusmod.</h3>
      <p>Lorem ipsum dolor sit amet, consectetur adipiscin elit, sed do eiusmod tempor incididunt ut labore et dolore magna aliqua. Ut enim ad minim veniam.</p>
    </article>
    <article class="post-card" style="left:439px">
      <div class="photo" role="img" aria-label="Scales of justice statue beside a laptop and paperwork" style="background:linear-gradient(135deg,#4a4136,#c9c6c0 50%,#6f6a62)"></div>
      <h3>Lorem ipsum dolor sit amet, consecte adipiscing elit, sed do eiusmod.</h3>
      <p>Lorem ipsum dolor sit amet, consectetur adipiscin elit, sed do eiusmod tempor incididunt ut labore et dolore magna aliqua. Ut enim ad minim veniam.</p>
    </article>
    <article class="post-card" style="left:800px">
      <div class="photo" role="img" aria-label="Distressed driver beside damaged cars after a collision" style="background:linear-gradient(135deg,#6b5648,#b9b6ae 45%,#2f4c78)"></div>
      <h3>Lorem ipsum dolor sit amet, consecte adipiscing elit, sed do eiusmod.</h3>
      <p>Lorem ipsum dolor sit amet, consectetur adipiscin elit, sed do eiusmod tempor incididunt ut labore et dolore magna aliqua. Ut enim ad minim veniam.</p>
    </article>
  </section>
</main>

<footer class="site-footer">
  <nav class="footer-links">
    <a style="left:79px" href="#">Practice Areas</a>
    <a style="left:213px" href="#">Attorneys</a>
    <a style="left:315px" href="#">Blog</a>
    <a style="left:392px" href="#">Contact us</a>
    <a style="left:510px" href="#">Things to do Before Filling For Divorce</a>
    <a style="left:806px" href="#">Things to do During Custrudy Battel</a>
  </nav>
  <div class="footer-rule"></div>
  <div class="contact-item" style="left:79px">
    <span class="contact-icon"><svg width="16" height="22" viewBox="0 0 16 22"><path d="M8 0C3.6 0 0 3.5 0 7.9 0 13.5 8 22 8 22s8-8.5 8-14.1C16 3.5 12.4 0 8 0zm0 11a3 3 0 110-6 3 3 0 010 6z" fill="#fff"/></svg></span>
    <span>48-2210 Alaula Road, Suite 212<br>Kailua Kona, Hawaii 96740.</span>
  </div>
  <div class="contact-item" style="left:494px">
    <span class="contact-icon"><svg width="20" height="20" viewBox="0 0 20 20"><path d="M3 1c1.5-1 2.8-.9 3.6.4l2 3.3c.6 1 .3 2-.6 2.7l-1.3 1c.9 2.5 2.6 4.2 5 5.1l1-1.3c.7-.9 1.7-1.2 2.7-.6l3.3 2c1.3.8 1.4 2.1.4 3.6-1.3 1.7-3.3 2.3-5.4 1.5C8.7 16.9 3.1 11.3 1.3 6.4.5 4.3 1.2 2.3 3 1z" fill="#fff"/></svg></span>
    <span>PHONE :<br>+1.808.555.0142</span>
  </div>
  <div class="contact-item" style="left:801px">
    <span class="contact-icon"><svg width="20" height="15" viewBox="0 0 20 15"><rect width="20" height="15" rx="1.5" fill="#fff"/><path d="M1 1.5l9 7 9-7" fill="none" stroke="#7b2d04" stroke-width="1.8"/></svg></span>
    <span>EMAIL :<br>clients@tarnadvocate.example</span>
  </div>
</footer>
<p class="copyright">©Meridian Crest Legal Group - 2019. All Rights Reserved.</p>

</body>
</html>
```